Interior Design/ decoration business card design

This card is for my Interior Design and Decoration business and later I will also be selling homewares. I would like the card to be very simple in design and like either white, duck egg blue , aquas or metallics on a flat mat card excellent quality card. It needs to be well designed as that is my field. I dont like fuss, the simpler the better. I would like a styalised brim under the name brim if possible. SIMPLE, STYLISH, CLASSIC, TASTEFUL

Target Market(s)

40 + year olds who are building or rennovating.

Industry/Entity Type

Business

Contact Information for Business Card

Brim
styling, design, homeware

Marnie Callow
p 0427163958
e marnie@brimhouse.com.au
w brimhouse.com.au

Requirements
Must have
• very simple, stylish, classic, sophisticated. Simple and easy to read text that is a print similar to attached image. I like simple round A's though not as in attached image.

Double sided. It wont save as double sided for some reason!!
Should not have
• not too much colour, No animated / cartoon pictures.

```html
<!DOCTYPE html>
<html lang="en">
<head>
<meta charset="utf-8">
<title>Brim business card, front and back</title>
<link href="https://fonts.googleapis.com/css2?family=Exo+2:wght@300;400;500&display=swap" rel="stylesheet">
<style>
  :root {
    --backdrop: #e8ecec;
    --card: #ffffff;
    --aqua: #5c9a98;
    --pewter: #7f878c;
    --duck-egg: #dcebe8;
    --ink: #2f3436;
    --soft-ink: #6d7679;
    --paper-text: #ffffff;
  }
  * { margin: 0; padding: 0; box-sizing: border-box; }
  html, body {
    width: 1200px;
    height: 974px;
    overflow: hidden;
    background: var(--backdrop);
    font-family: "Exo 2", sans-serif;
    color: var(--ink);
  }
  .stage { position: relative; width: 1200px; height: 974px; }

  .card {
    position: absolute;
    top: 102px;
    width: 440px;
    height: 770px;
    background: var(--card);
    overflow: hidden;
    box-shadow: 0 10px 30px rgba(0,0,0,0.14);
  }
  .card--front { left: 120px; }
  .card--back { left: 640px; }

  .wordmark {
    position: absolute;
    left: 0;
    right: 0;
    text-align: center;
    font-weight: 300;
    font-size: 64px;
    line-height: 1;
    letter-spacing: 2px;
    color: var(--ink);
  }
  .card--front .wordmark { top: 270px; }
  .card--back .wordmark { top: 84px; }

  .tagline {
    position: absolute;
    left: 0;
    right: 0;
    text-align: center;
    font-weight: 300;
    font-size: 16px;
    letter-spacing: 3px;
    color: var(--soft-ink);
    text-transform: lowercase;
  }
  .card--front .tagline { top: 352px; }

  .footer-tab {
    position: absolute;
    left: 0;
    right: 0;
    bottom: 0;
    height: 120px;
    display: flex;
    align-items: center;
    justify-content: center;
    color: var(--paper-text);
    font-size: 19px;
    letter-spacing: 1.5px;
  }
  .card--front .footer-tab { background: var(--aqua); border-radius: 0 34px 0 0; }
  .card--back .footer-tab { background: var(--pewter); border-radius: 34px 0 0 0; letter-spacing: 3px; font-weight: 300; }

  .name-band {
    position: absolute;
    top: 200px;
    left: 0;
    right: 0;
    height: 110px;
    background: var(--aqua);
    color: var(--paper-text);
    display: flex;
    flex-direction: column;
    justify-content: center;
    padding-left: 150px;
    text-transform: uppercase;
  }
  .name-band .person { font-size: 28px; font-weight: 400; letter-spacing: 2px; }
  .name-band .role { font-size: 17px; font-weight: 300; letter-spacing: 2px; margin-top: 4px; }

  .contact-row {
    position: absolute;
    left: 0;
    right: 0;
    display: flex;
    align-items: center;
    gap: 40px;
    padding-left: 60px;
    font-size: 18px;
    letter-spacing: 1px;
  }
  .contact-row svg { width: 50px; height: 50px; flex: none; }
  .icon-solid { fill: var(--ink); }
  .icon-line { fill: none; stroke: var(--ink); stroke-width: 1.6; }
  .contact-row--phone { top: 330px; height: 110px; }
  .contact-row--email { top: 450px; height: 100px; background: var(--duck-egg); }
  .contact-row--web { top: 560px; height: 90px; }
</style>
</head>
<body>
<main class="stage">

  <section class="card card--front" aria-label="Card front">
    <div class="wordmark">brim</div>
    <div class="tagline">styling, design, homeware</div>
    <div class="footer-tab">www.brimhouse.com.au</div>
  </section>

  <section class="card card--back" aria-label="Card back">
    <div class="wordmark">brim</div>

    <div class="name-band">
      <span class="person">Marnie Callow</span>
      <span class="role">General Manager</span>
    </div>

    <div class="contact-row contact-row--phone">
      <svg viewBox="0 0 24 24" aria-hidden="true"><path class="icon-solid" d="M6.6 10.8a15.1 15.1 0 0 0 6.6 6.6l2.2-2.2a1 1 0 0 1 1-.25 11.4 11.4 0 0 0 3.6.57 1 1 0 0 1 1 1V20a1 1 0 0 1-1 1A17 17 0 0 1 3 4a1 1 0 0 1 1-1h3.5a1 1 0 0 1 1 1c0 1.25.2 2.45.57 3.6a1 1 0 0 1-.25 1z"/></svg>
      <div>0427 163 958</div>
    </div>

    <div class="contact-row contact-row--email">
      <svg viewBox="0 0 24 24" aria-hidden="true"><path class="icon-line" d="M2 5h20v14H2z"/><path class="icon-line" d="M2 5l10 8 10-8"/></svg>
      <div>marnie@brimhouse.com.au</div>
    </div>

    <div class="contact-row contact-row--web">
      <svg viewBox="0 0 24 24" aria-hidden="true"><circle class="icon-line" cx="12" cy="12" r="9"/><path class="icon-line" d="M3 12h18M12 3c3 3 3 15 0 18M12 3c-3 3-3 15 0 18"/></svg>
      <div>brimhouse.com.au</div>
    </div>

    <div class="footer-tab">styling, design, homeware</div>
  </section>

</main>
</body>
</html>
```